WordPress Design for both website and landing page for an expert

I need a clean and stylish design for my new website. I work as an expert (see attached file WHY HOW WHAT), my product is expert opinion (reports) for company evaluations You can use all of the attached pictures colored or black / white. The person is me, you can add other pictures, if you want. The design should be clean and stylish, so you could use white, black, gray, silver and / or one additional color. I have added an idea about my website, see attached file CONCEPT WEBSITE If you have any more information, please do not hesitate to contact us 'Hesitate to ask me ...

```html
<!DOCTYPE html>
<html lang="en">
<head>
<meta charset="utf-8">
<title>Lukas Berndt – What I do</title>
<link rel="stylesheet" href="https://fonts.googleapis.com/css2?family=Montserrat:wght@400;500;600&family=Noto+Serif:wght@400&display=swap">
<style>
  :root {
    --ink: #23262b;
    --ink-soft: #3d4046;
    --muted: #8c8f94;
    --nav-active: #a4a6aa;
    --white: #ffffff;
    --band: #eef2f5;
    --footer: #3a3e45;
    --footer-text: #b9bcc1;
    --button-line: #9a9da2;
    --scroll-btn: #80848a;
  }
  * { box-sizing: border-box; margin: 0; padding: 0; }
  html, body {
    width: 1157px; height: 1200px; overflow: hidden;
    background: var(--white);
    font-family: "Montserrat", Arial, sans-serif;
    color: var(--ink);
  }
  .page { position: relative; width: 1157px; height: 1200px; }

  .brand {
    position: absolute; left: 65px; top: 40px;
    display: flex; align-items: center; gap: 12px;
    font-size: 19px; font-weight: 500; letter-spacing: 3px;
    color: var(--ink);
  }
  .brand-mark { width: 14px; height: 14px; background: var(--ink); }

  .main-nav {
    position: absolute; top: 58px; right: 67px;
    display: flex; gap: 33px;
    font-size: 11.5px; font-weight: 500; letter-spacing: 2px;
  }
  .main-nav a { color: var(--ink); text-decoration: none; }
  .main-nav a.is-active { color: var(--nav-active); }

  .hero {
    position: absolute; left: 133px; top: 189px;
    width: 891px; height: 363px;
    background:
      linear-gradient(100deg, rgba(60,70,110,.55) 0%, rgba(180,170,170,.2) 45%, rgba(90,110,150,.45) 100%),
      linear-gradient(180deg, #c9c8cf 0%, #b7b2b4 45%, #9ea2b3 100%);
  }
  .hero-title {
    position: absolute; inset: 0;
    display: flex; align-items: center; justify-content: center;
    color: var(--white); font-size: 40px; font-weight: 500; letter-spacing: 3px;
  }

  .services-title {
    position: absolute; left: 0; width: 100%; top: 604px;
    text-align: center; font-size: 26px; font-weight: 500; line-height: 38px;
  }
  .service-list { position: absolute; top: 713px; left: 0; width: 100%; }
  .service {
    position: absolute; width: 185px;
    font-family: "Noto Serif", Georgia, serif;
    font-size: 15.5px; line-height: 24.5px; color: var(--muted);
  }
  .service-dots {
    display: block; font-size: 12px; line-height: 16px; color: var(--ink-soft);
  }

  .cta-band {
    position: absolute; left: 0; top: 865px; width: 100%; height: 268px;
    background: var(--band);
  }
  .cta-title {
    position: absolute; left: 0; width: 100%; top: 55px;
    text-align: center; font-size: 26px; font-weight: 500; line-height: 38px;
  }
  .cta-button {
    position: absolute; left: 476px; top: 163px; width: 205px; height: 39px;
    border: 1.5px solid var(--button-line); border-radius: 20px;
    display: flex; align-items: center; justify-content: center;
    font-size: 11.5px; font-weight: 600; letter-spacing: 1.5px;
    color: var(--ink); text-decoration: none;
  }

  .site-footer {
    position: absolute; left: 0; top: 1133px; width: 100%; height: 67px;
    background: var(--footer); color: var(--footer-text);
    font-size: 11px;
  }
  .copyright { position: absolute; left: 132px; top: 27px; }
  .legal-links { position: absolute; right: 131px; top: 27px; display: flex; gap: 10px; }
  .legal-links a { color: var(--footer-text); text-decoration: none; }
  .scroll-top { position: absolute; left: 1070px; top: 13px; }
</style>
</head>
<body>
<div class="page">
  <header>
    <div class="brand"><span class="brand-mark"></span>LUKAS BERNDT</div>
    <nav class="main-nav">
      <a href="#">HOME</a>
      <a href="#">ABOUT</a>
      <a href="#" class="is-active">WHAT I DO</a>
      <a href="#">WHY / HOW I DO</a>
      <a href="#">CONTACT</a>
    </nav>
  </header>

  <section class="hero" role="img" aria-label="Hands typing on a keyboard at a desk with a tablet, glasses and financial charts">
    <h1 class="hero-title">WHAT I DO</h1>
  </section>

  <h2 class="services-title">Conducting business valuations<br>in case of ...</h2>
  <div class="service-list">
    <p class="service" style="left:273px"><span class="service-dots">...</span>Buying / selling shares or entire companies</p>
    <p class="service" style="left:487px"><span class="service-dots">...</span>Inheritance matters</p>
    <p class="service" style="left:703px"><span class="service-dots">...</span>Questions in the gain compensation (in divorces)</p>
  </div>

  <section class="cta-band">
    <h2 class="cta-title">You need an opinion to determine<br>the value of your company</h2>
    <a class="cta-button" href="#">CONTACT NOW!</a>
  </section>

  <footer class="site-footer">
    <span class="copyright">© 2018 Lukas M. Berndt. All Rights Reserved</span>
    <nav class="legal-links">
      <a href="#">Data protection</a><span>I</span>
      <a href="#">Cookies</a><span>I</span>
      <a href="#">imprint</a>
    </nav>
    <svg class="scroll-top" width="41" height="41" viewBox="0 0 41 41" aria-label="Back to top">
      <circle cx="20.5" cy="20.5" r="20" fill="var(--scroll-btn)"/>
      <path d="M20.5 26 V15 M16.5 19 L20.5 15 L24.5 19" stroke="#ffffff" stroke-width="1.3" fill="none"/>
    </svg>
  </footer>
</div>
</body>
</html>
```